Moravel Aesthetic Doctor

I require an elegant, luxurious looking business card for my aesthetic business. I am a doctor and that will set me aside from competitors. I am planning to provide home and spa based treatments to clients with high expectations. I have attached my logo.

```html
<!DOCTYPE html>
<html lang="en">
<head>
<meta charset="utf-8">
<title>Moravel Aesthetic Doctor – Business Card</title>
<link href="https://fonts.googleapis.com/css2?family=Lato:wght@400&family=Montserrat:wght@400;500&display=swap" rel="stylesheet">
<style>
  :root {
    --backdrop: #2a2a2a;
    --card: #ffffff;
    --brand-blue: #2a8fd6;
    --brand-grey: #9a9ea4;
    --text-dark: #4a4a4a;
    --text-mid: #606060;
    --icon-blue: #3b83c9;
  }
  * { margin: 0; padding: 0; box-sizing: border-box; }
  html, body {
    width: 1200px; height: 1192px; overflow: hidden;
    background: var(--backdrop);
  }
  .canvas { position: relative; width: 1200px; height: 1192px; }
  .card {
    position: absolute; left: 189px; width: 827px; height: 469px;
    background: var(--card); border-radius: 27px;
  }
  .card--front { top: 112px; }
  .card--back { top: 616px; }

  .wordmark {
    position: absolute; display: flex; align-items: center; gap: 14px;
    font-family: "Lato", sans-serif; font-weight: 400; color: var(--brand-grey);
  }
  .wordmark__dot { border-radius: 50%; background: var(--brand-grey); flex: none; }
  .wordmark__text { display: flex; flex-direction: column; line-height: 1; text-transform: uppercase; }
  .card--front .wordmark { left: 72px; top: 184px; }
  .card--front .wordmark__dot { width: 34px; height: 34px; }
  .card--front .wordmark__name { font-size: 52px; letter-spacing: 1px; }
  .card--front .wordmark__role { font-size: 19px; letter-spacing: 1px; margin-top: 6px; }
  .card--back .wordmark { left: 50%; transform: translateX(-50%); top: 140px; gap: 22px; }
  .card--back .wordmark__dot { width: 52px; height: 52px; }
  .card--back .wordmark__name { font-size: 86px; letter-spacing: 2px; }
  .card--back .wordmark__role { font-size: 32px; letter-spacing: 1.5px; margin-top: 10px; }

  .divider {
    position: absolute; left: 426px; top: 151px; width: 2px; height: 166px;
    background: var(--brand-blue);
  }
  .contact { position: absolute; left: 452px; top: 146px; font-family: "Montserrat", sans-serif; }
  .contact__name { font-size: 21px; font-weight: 500; color: var(--brand-blue); }
  .contact__creds { font-size: 12px; color: var(--text-mid); margin-left: 4px; }
  .contact__qual { font-size: 18.5px; color: var(--text-dark); line-height: 24px; margin-top: 6px; }
  .contact__list { list-style: none; margin-top: 19px; }
  .contact__item {
    display: flex; align-items: center; gap: 10px;
    font-size: 18.5px; color: var(--text-dark); height: 25px;
  }
  .contact__item svg { width: 14px; height: 14px; flex: none; }
  .social { display: inline-flex; gap: 12px; margin-left: 50px; }
  .social span { width: 14px; height: 14px; border-radius: 50%; background: var(--icon-blue); }

  .services {
    position: absolute; left: 0; right: 0; top: 412px; text-align: center;
    font-family: "Lato", sans-serif; font-size: 18.5px; color: var(--text-mid);
  }
  .tagline {
    position: absolute; left: 0; right: 0; top: 378px; text-align: center;
    font-family: "Lato", sans-serif; font-size: 31px; color: #7a7a7a;
  }
</style>
</head>
<body>
<main class="canvas">
  <section class="card card--front">
    <div class="wordmark">
      <span class="wordmark__dot"></span>
      <span class="wordmark__text">
        <span class="wordmark__name">Moravel</span>
        <span class="wordmark__role">Aesthetic Doctor</span>
      </span>
    </div>
    <div class="divider"></div>
    <div class="contact">
      <p><span class="contact__name">Dr Elise Varnholt</span><span class="contact__creds">MRCPCH MD</span></p>
      <p class="contact__qual">Australasian Diploma<br>&nbsp;of Aesthetic Medicine</p>
      <ul class="contact__list">
        <li class="contact__item">
          <svg viewBox="0 0 24 24"><path fill="#3b83c9" d="M6.6 10.8a15 15 0 0 0 6.6 6.6l2.2-2.2c.3-.3.7-.4 1-.2 1.1.4 2.3.6 3.6.6.6 0 1 .4 1 1V20c0 .6-.4 1-1 1A17 17 0 0 1 3 4c0-.6.4-1 1-1h3.5c.6 0 1 .4 1 1 0 1.3.2 2.5.6 3.6.1.3 0 .7-.2 1z"/></svg>
          0800 555 018
        </li>
        <li class="contact__item">
          <svg viewBox="0 0 24 24"><path fill="#3b83c9" d="M2 5h20v14H2z"/><path fill="none" stroke="#fff" stroke-width="1.8" d="M2 5l10 8 10-8"/></svg>
          elise@moravel.co.nz
        </li>
        <li class="contact__item">
          <svg viewBox="0 0 24 24" fill="none" stroke="#3b83c9" stroke-width="2"><circle cx="12" cy="12" r="10"/><path d="M2 12h20M12 2c3 3 3 17 0 20M12 2c-3 3-3 17 0 20"/></svg>
          www.moravel.co.nz
          <span class="social"><span></span><span></span></span>
        </li>
      </ul>
    </div>
    <p class="services">Dermal injectables - Plasma facials - Microneedling Skin boosters - Excessive sweating</p>
  </section>

  <section class="card card--back">
    <div class="wordmark">
      <span class="wordmark__dot"></span>
      <span class="wordmark__text">
        <span class="wordmark__name">Moravel</span>
        <span class="wordmark__role">Aesthetic Doctor</span>
      </span>
    </div>
    <p class="tagline">Home and Spa Based Treatments</p>
  </section>
</main>
</body>
</html>
```